Animal Eye Clinic needs a Business card

We are a new veterinary ophthalmology practice (Ridgeline Pet Vision Care) and we need a business card designed. We only see animal eyes - we are not a regular veterinary clinic. We already have a logo. We are looking for a professional, good looking business card to hand out to our clients. We are looking for something simple but professional and contemporary. Our logo is likely the only picture/graphic that needs to be on the card.
Updates

Contact Information for Business Card

Delia Vossman, BSc, DVM, MSc, DipACVO
Veterinary Ophthalmologist

Phone: 250.418.3927
Email: ridgelinepetvisioncare@mailbox-example.net
Website: ridgelinepetvisioncare-example.net
Address: 1874 Thornbury Rd
Kelowna, BC, V1X 4M9

Colors

Designer to choose colors to be used in the design.

Requirements
Must have
• Our logo (attached)

```html
<!DOCTYPE html>
<html lang="en">
<head>
<meta charset="utf-8">
<title>Ridgeline Pet Vision Care – Business Card</title>
<link href="https://fonts.googleapis.com/css2?family=Arimo:wght@400;700&display=swap" rel="stylesheet">
<style>
  :root {
    --teal: #1a95a5;
    --grey-text: #6d6f72;
    --card: #ffffff;
    --backdrop: #2b2c30;
    --faint-mark: #eef2f2;
  }
  * { box-sizing: border-box; margin: 0; padding: 0; }
  html, body { width: 1200px; height: 800px; overflow: hidden; }
  body {
    background: var(--backdrop);
    font-family: "Arimo", Arial, sans-serif;
    display: flex;
    align-items: center;
    justify-content: center;
    gap: 48px;
  }
  .card {
    position: relative;
    width: 525px;
    height: 300px;
    background: var(--card);
    border-radius: 22px;
    overflow: hidden;
    box-shadow: 0 14px 30px rgba(0,0,0,.35);
  }

  /* Front */
  .card-front {
    display: flex;
    align-items: center;
    justify-content: center;
  }
  .brand {
    display: flex;
    align-items: center;
    gap: 14px;
    color: var(--teal);
    font-weight: 700;
    white-space: nowrap;
  }
  .brand-dot {
    width: 42px; height: 42px;
    border-radius: 50%;
    background: var(--teal);
    flex: none;
  }
  .card-front .brand-name { font-size: 27px; letter-spacing: .5px; }

  /* Back */
  .faint-mark {
    position: absolute;
    right: -40px;
    top: -30px;
    width: 260px;
    height: 260px;
    border-radius: 50%;
    background: var(--faint-mark);
  }
  .contact {
    position: absolute;
    left: 34px;
    top: 40px;
    color: var(--grey-text);
    font-size: 12.5px;
    line-height: 1.35;
  }
  .person-name { font-size: 17px; color: var(--teal); }
  .person-name strong { font-weight: 700; }
  .person-creds { font-weight: 400; }
  .person-role { margin-bottom: 22px; }
  .address { margin-bottom: 18px; }
  .contact-line { display: flex; align-items: center; gap: 7px; margin-bottom: 2px; }
  .icon { width: 14px; height: 14px; flex: none; }
  .card-back .brand {
    position: absolute;
    left: 34px;
    bottom: 30px;
  }
  .card-back .brand-name { font-size: 19px; }
</style>
</head>
<body>

  <section class="card card-front">
    <div class="brand">
      <span class="brand-dot"></span>
      <span class="brand-name">Ridgeline Pet Vision Care</span>
    </div>
  </section>

  <section class="card card-back">
    <div class="faint-mark"></div>
    <div class="contact">
      <p class="person-name"><strong>Delia Vossman</strong><span class="person-creds">, BSc, DVM, MSc, DipACVO</span></p>
      <p class="person-role">Veterinary Ophthalmologist</p>
      <p class="address">1874 Thornbury Rd<br>Kelowna, BC, V1X 4M9</p>
      <p class="contact-line">
        <svg class="icon" viewBox="0 0 14 14"><circle cx="7" cy="7" r="7" fill="var(--teal)"/><path d="M4.5 3.5l1.5 0 .6 1.8-.9.7a5 5 0 0 0 2.3 2.3l.7-.9 1.8.6v1.5c0 .4-.3.6-.7.6A6 6 0 0 1 3.9 4.2c0-.4.2-.7.6-.7z" fill="#fff"/></svg>
        250.418.3927
      </p>
      <p class="contact-line">
        <svg class="icon" viewBox="0 0 14 14"><circle cx="7" cy="7" r="7" fill="var(--teal)"/><rect x="3.5" y="4.5" width="7" height="5" fill="none" stroke="#fff" stroke-width="1"/><path d="M3.5 4.5L7 7.3l3.5-2.8" fill="none" stroke="#fff" stroke-width="1"/></svg>
        ridgelinepetvisioncare@mailbox-example.net
      </p>
      <p class="contact-line">
        <svg class="icon" viewBox="0 0 14 14"><circle cx="7" cy="7" r="7" fill="var(--teal)"/><circle cx="7" cy="7" r="3.8" fill="none" stroke="#fff" stroke-width="1"/><ellipse cx="7" cy="7" rx="1.6" ry="3.8" fill="none" stroke="#fff" stroke-width=".9"/><path d="M3.2 7h7.6" stroke="#fff" stroke-width=".9"/></svg>
        ridgelinepetvisioncare-example.net
      </p>
    </div>
    <div class="brand">
      <span class="brand-name">Ridgeline Pet Vision Care</span>
    </div>
  </section>

</body>
</html>
```